I am a general contractor in Portland, Or. I would like a clean and simple design layout, maybe using the "didot" font, blue and dark bronze in colors are preferred. On one side of the card, it would be nice to have a logo(attached photo) and business name(KTW Construction). I don't need my job title on the card, just some thing along the lines of "gordon pike, general contractor". Thanks much.

Target Market(s)

Adults from 30-55 years old. Middle to upper class.

Industry/Entity Type

Contractor

Contact Information for Business Card

KTW Construction
Gordon L. Pike
2843 NE 71st Ave.
Portland, Or. 97288
541.555.0187

Font styles to use
Other font styles liked:
• didot

Colors
3277b5
7f7f7f

Requirements
Should not have
• Too much going on.

```html
<!DOCTYPE html>
<html lang="en">
<head>
<meta charset="utf-8">
<title>KTW Construction – Business Card</title>
<link rel="stylesheet" href="https://fonts.googleapis.com/css2?family=Lato:wght@400;700;900&display=swap">
<style>
  :root {
    --brand-blue: #3277b5;
    --brand-blue-dark: #245d92;
    --brand-blue-light: #4a8cc6;
    --text-grey: #7f7f7f;
    --card-white: #ffffff;
    --card-white-shade: #eef1f4;
    --stage: #2e2e2e;
  }
  * { margin: 0; padding: 0; box-sizing: border-box; }
  html, body {
    width: 1200px;
    height: 997px;
    overflow: hidden;
    background: var(--stage);
    font-family: "Lato", Arial, sans-serif;
  }
  .stage {
    position: relative;
    width: 1200px;
    height: 997px;
  }
  .card {
    position: absolute;
    width: 620px;
    height: 354px;
    border-radius: 22px;
  }
  .card-front {
    left: 290px;
    top: 118px;
    background: radial-gradient(ellipse at 60% 40%, var(--brand-blue-light), var(--brand-blue) 55%, var(--brand-blue-dark));
  }
  .card-back {
    left: 290px;
    top: 525px;
    background: linear-gradient(180deg, var(--card-white), var(--card-white-shade));
  }
  .card-frame {
    position: absolute;
    inset: 12px;
    border-radius: 14px;
  }
  .card-front .card-frame { border: 3px solid var(--card-white); }
  .card-back .card-frame { border: 5px solid var(--brand-blue); }

  .brand {
    position: absolute;
    display: flex;
    align-items: center;
    gap: 14px;
  }
  .brand-dot {
    width: 26px;
    height: 26px;
    border-radius: 50%;
  }
  .brand-name {
    font-weight: 900;
    letter-spacing: 0.5px;
    text-transform: uppercase;
  }
  .card-front .brand {
    left: 0; right: 0; top: 155px;
    justify-content: center;
  }
  .card-front .brand-dot { background: var(--card-white); }
  .card-front .brand-name { color: var(--card-white); font-size: 30px; }

  .card-back .brand { left: 58px; top: 70px; }
  .card-back .brand-dot { background: var(--brand-blue); }
  .card-back .brand-name { color: var(--brand-blue); font-size: 26px; }

  .contact {
    position: absolute;
    left: 340px;
    top: 150px;
    list-style: none;
    color: var(--text-grey);
    font-size: 15px;
    line-height: 1.3;
  }
  .contact-item {
    display: flex;
    align-items: flex-start;
    gap: 10px;
    margin-bottom: 10px;
  }
  .contact-icon { flex: 0 0 22px; width: 22px; height: 22px; }

  .person {
    position: absolute;
    left: 58px;
    bottom: 62px;
  }
  .person-name {
    color: var(--brand-blue);
    font-weight: 900;
    font-size: 28px;
    line-height: 1.1;
  }
  .person-role {
    color: var(--text-grey);
    font-weight: 700;
    font-size: 16px;
    letter-spacing: 0.5px;
    text-transform: uppercase;
  }
</style>
</head>
<body>
<main class="stage">

  <section class="card card-front" aria-label="Business card front">
    <div class="card-frame"></div>
    <div class="brand">
      <span class="brand-dot"></span>
      <span class="brand-name">KTW Construction</span>
    </div>
  </section>

  <section class="card card-back" aria-label="Business card back">
    <div class="card-frame"></div>
    <div class="brand">
      <span class="brand-dot"></span>
      <span class="brand-name">KTW Construction</span>
    </div>

    <ul class="contact">
      <li class="contact-item">
        <svg class="contact-icon" viewBox="0 0 22 22" aria-hidden="true">
          <circle cx="11" cy="11" r="11" fill="var(--brand-blue)"/>
          <path d="M7.5 6c.6-.4 1.3-.3 1.6.3l.9 1.7c.3.5.1 1.1-.3 1.4l-.6.5c.6 1.3 1.6 2.3 2.9 2.9l.5-.6c.3-.4.9-.6 1.4-.3l1.7.9c.6.3.7 1 .3 1.6l-.7.8c-.6.6-1.5.8-2.3.4-2.7-1.2-4.8-3.3-6-6-.4-.8-.2-1.7.4-2.3z" fill="#fff"/>
        </svg>
        <span>541.555.0187</span>
      </li>
      <li class="contact-item">
        <svg class="contact-icon" viewBox="0 0 22 22" aria-hidden="true">
          <circle cx="11" cy="11" r="11" fill="var(--brand-blue)"/>
          <path d="M11 4.5a4.3 4.3 0 0 0-4.3 4.3c0 3.2 4.3 8.2 4.3 8.2s4.3-5 4.3-8.2A4.3 4.3 0 0 0 11 4.5zm0 6a1.7 1.7 0 1 1 0-3.4 1.7 1.7 0 0 1 0 3.4z" fill="#fff"/>
        </svg>
        <span>2843 NE 71st Ave. Portland,<br>Oregon 97288</span>
      </li>
    </ul>

    <div class="person">
      <p class="person-name">Gordon L. Pike</p>
      <p class="person-role">General Contractor</p>
    </div>
  </section>

</main>
</body>
</html>
```